Business Card Design Project

We are not a new company, but renamed to "Vantorin Kitchens" last year. We specialize in modern high-end cabinetry imports. We would like to communicate a sense of quality and cutting edge technology. Ideally the design would incorporate our logo colors, silver, red and preferably a black, matte background. Though we are open to suggestions.
Logo is attached.
Edit: I have attached rough drafts of the previous cards, this way you will have all necessary content that needs to go on the cards.
Updates
Project Deadline Extended
Reason: We have received a lot of great designs, but due to the sheer number we couldn't respond to all. We will extend the deadline for another 7 days to finalize and provide feedback to designers.
Thank you for your hard work!
Industry/Entity Type
Business
Look and feel
Each slider illustrates characteristics of the customer's brand and the style your logo design should communicate.

```html
<!DOCTYPE html>
<html lang="en">
<head>
<meta charset="utf-8">
<title>Vantorin Kitchens – Business Card</title>
<link href="https://fonts.googleapis.com/css2?family=Roboto:wght@400;700&display=swap" rel="stylesheet">
<style>
  :root {
    --backdrop: #b8c8c7;
    --card-dark: #161616;
    --card-mid: #3a3a3a;
    --silver: #b9bbbe;
    --silver-dark: #8a8c8f;
    --white: #f2f2f2;
    --red: #e11b22;
    --grey-band: #8f9093;
  }
  * { box-sizing: border-box; margin: 0; padding: 0; }
  html, body {
    width: 1200px; height: 973px; overflow: hidden;
    background: var(--backdrop);
    font-family: "Roboto", Arial, sans-serif;
  }
  .card {
    position: absolute;
    left: 250px;
    width: 700px; height: 400px;
    overflow: hidden;
    background: radial-gradient(ellipse at 50% 35%, var(--card-mid) 0%, var(--card-dark) 70%);
    box-shadow: 0 8px 22px rgba(0,0,0,.25);
  }
  .card--front { top: 50px; }
  .card--back { top: 523px; display: flex; align-items: center; justify-content: center; }

  .wordmark {
    position: absolute; left: 0; right: 0; top: 105px;
    text-align: center;
    font-weight: 700; font-size: 40px; letter-spacing: 3px;
    text-transform: uppercase; color: var(--silver);
  }
  .card--back .wordmark {
    position: static; font-size: 58px; letter-spacing: 4px;
  }

  .identity {
    position: absolute; right: 370px; top: 196px;
    text-align: right; color: var(--white);
  }
  .identity__name { font-weight: 700; font-size: 18px; letter-spacing: .5px; }
  .identity__title { font-size: 14px; margin-top: 3px; color: #d6d6d6; }
  .identity__address { font-size: 15px; margin-top: 18px; line-height: 1.4; color: #e4e4e4; }

  .divider {
    position: absolute; left: 345px; top: 192px;
    width: 1px; height: 118px; background: #6a6a6a;
  }

  .contacts {
    position: absolute; left: 360px; top: 190px;
    list-style: none; color: var(--white); font-size: 15px;
  }
  .contacts li { display: flex; align-items: center; height: 25px; }
  .contacts svg { width: 14px; height: 14px; margin-right: 9px; flex: none; }

  .bands { position: absolute; left: 0; bottom: 0; width: 700px; height: 400px; }
</style>
</head>
<body>

<section class="card card--front">
  <div class="wordmark">Vantorin Kitchens</div>

  <div class="identity">
    <div class="identity__name">MARCUS DELANE</div>
    <div class="identity__title">Director</div>
    <div class="identity__address">2218 - 84 Ave. Edmonton<br>AB T5K 3R2</div>
  </div>

  <div class="divider"></div>

  <ul class="contacts">
    <li>
      <svg viewBox="0 0 14 14" aria-hidden="true"><circle cx="7" cy="7" r="6.3" fill="none" stroke="var(--red)" stroke-width="1.4"/><path d="M4.6 3.8l1.4 1.6-.8.9c.5 1 1.3 1.8 2.3 2.3l.9-.8 1.6 1.4-.8 1.1C6.9 10 4 7.1 3.7 4.6z" fill="var(--red)"/></svg>
      780.512.0846
    </li>
    <li>
      <svg viewBox="0 0 14 14" aria-hidden="true"><path d="M2 6c3-3 7-3 10 0l-1.6 1.6-1.8-1V5.2c-1.1-.4-2.1-.4-3.2 0v1.4l-1.8 1z M3.5 9h7v3h-7z" fill="var(--red)"/></svg>
      780.512.0847
    </li>
    <li>
      <svg viewBox="0 0 14 14" aria-hidden="true"><rect x="4" y="1" width="6" height="12" rx="1.2" fill="var(--red)"/><rect x="5" y="2.5" width="4" height="7" fill="var(--card-dark)"/></svg>
      780.619.3352
    </li>
    <li>
      <svg viewBox="0 0 14 14" aria-hidden="true"><circle cx="7" cy="7" r="6.3" fill="var(--red)"/><path d="M3.8 5h6.4v4.2H3.8z M3.8 5L7 7.4 10.2 5" fill="none" stroke="#fff" stroke-width=".9"/></svg>
      marcus@vantorinkitchens.ca
    </li>
  </ul>

  <svg class="bands" viewBox="0 0 700 400" aria-hidden="true">
    <polygon points="0,376 300,376 330,346 700,346 700,356 336,356 306,388 0,388" fill="var(--red)"/>
    <polygon points="360,330 700,330 700,344 346,344 " fill="var(--grey-band)"/>
    <polygon points="0,388 306,388 336,356 700,356 700,400 0,400" fill="#1b1b1b"/>
  </svg>
</section>

<section class="card card--back">
  <div class="wordmark">Vantorin Kitchens</div>
</section>

</body>
</html>
```